Maplecrest Disability - Social Security Disability Attorneys

Our company is expanding to attract clients nationwide for our social security disability practice. We have a logo, but I am looking for a creative and elegant letterhead that projects an image of being technologically advanced but still professional enough for the legal field. I am looking for the "wow factor" combined with this is still professional enough for a law practice.

Requesting letterhead and business card design
Updates

Had to update and change the logo. The previous logo had a typo. Please send updates with the new logo for consideration. The letterhead and business cards should be professional enough to be used for a law firm. Thanks.

Industry/Entity Type

Law Practice, Law Firm, Healthcare Industry, Government

Colors

Designer to choose colors to be used in the design.

Requirements
Nice to have
• **Please create a vertical design for the business card**

```html
<!DOCTYPE html>
<html lang="en">
<head>
<meta charset="utf-8">
<title>Maplecrest Disability Letterhead</title>
<link href="https://fonts.googleapis.com/css2?family=Tinos:wght@400&family=Open+Sans:wght@400;600&display=swap" rel="stylesheet">
<style>
  :root{
    --canvas:#2b2b2d;
    --paper:#ffffff;
    --paper-shade:#e9e9ec;
    --brand-blue:#1f6fb5;
    --ink:#1a1a1a;
    --muted:#444448;
    --band-top:#ffffff;
    --band-bottom:#e2e2e6;
    --footer-strip:#f1f1f3;
  }
  *{margin:0;padding:0;box-sizing:border-box}
  html,body{width:1200px;height:900px;overflow:hidden;background:var(--canvas)}
  .letterhead{
    position:absolute;left:250px;top:12px;width:700px;height:876px;overflow:hidden;
    background:linear-gradient(180deg,var(--paper-shade) 0,var(--paper) 90px,var(--paper) 100%);
    box-shadow:0 6px 24px rgba(0,0,0,.5);
    font-family:"Tinos","Times New Roman",serif;color:var(--ink);
  }
  .brand{position:absolute;top:66px;left:0;width:100%;text-align:center}
  .brand-name{display:inline-flex;align-items:center;gap:8px;font-size:19px;color:var(--brand-blue);letter-spacing:.5px}
  .brand-dot{width:9px;height:9px;border-radius:50%;background:var(--brand-blue)}
  .brand-tagline{margin-top:6px;font-family:"Open Sans",Arial,sans-serif;font-size:8.5px;letter-spacing:2.6px;color:var(--muted)}
  .recipient{position:absolute;top:190px;left:100px;display:flex;gap:26px;font-size:12.5px;line-height:14.5px}
  .recipient address{font-style:normal}
  .letter-body{position:absolute;top:272px;left:96px;width:520px;font-size:12.5px;line-height:14.6px}
  .salutation{margin-bottom:14px}
  .letter-body p.para{margin-bottom:15px}
  .closing{margin-top:2px}
  .signature{display:block;margin-top:6px;width:150px;height:40px;background:linear-gradient(90deg,rgba(27,42,140,.18),rgba(27,42,140,.05))}
  .footer-band{position:absolute;left:0;bottom:46px;width:100%;height:90px;background:linear-gradient(180deg,var(--band-top) 0,var(--band-bottom) 100%)}
  .footer-strip{position:absolute;left:0;bottom:0;width:100%;height:46px;background:var(--footer-strip)}
  .footer{position:absolute;bottom:14px;width:100%;text-align:center;font-family:"Open Sans",Arial,sans-serif;font-size:8px;line-height:12px;color:var(--muted)}
  .footer b{font-weight:600}
</style>
</head>
<body>
<main class="letterhead">
  <header class="brand">
    <div class="brand-name"><span class="brand-dot"></span>Maplecrest Disability</div>
    <div class="brand-tagline">SOCIAL SECURITY DISABILITY ATTORNEYS</div>
  </header>

  <section class="recipient">
    <span>To:</span>
    <address>Mr./Mrs. Customerand Partner<br>100 Good Avenue<br>New York<br>NY 55254</address>
  </section>

  <section class="letter-body">
    <p class="salutation">Dear Customer,</p>
    <p class="para">Lorem ipsum dolor sit amet, consetetur sadipscing elitr, sed diam nonumy eirmod tempor invidunt ut labore et dolore magna aliquyam erat, sed diam voluptua. At vero eos et accusam et justo duo dolores et ea rebum. Stet clita kasd gubergren, no sea takimata sanctus est Lorem ipsum dolor sit amet. Lorem ipsum dolor sit amet, consetetur sadipscing elitr, sed diam nonumy eirmod tempor invidunt ut labore et dolore magna aliquyam erat, sed diam voluptua. At vero eos et accusam et justo duo dolores et ea rebum. Stet clita kasd gubergren, no sea takimata sanctus est Lorem ipsum dolor sit amet. Lorem ipsum dolor sit amet, consetetur sadipscing elitr, sed diam nonumy eirmod tempor invidunt ut labore et dolore magna aliquyam erat, sed diam voluptua. At vero eos et accusam et justo duo dolores et ea rebum. Stet clita kasd gubergren, no sea takimata sanctus est Lorem ipsum dolor sit amet.</p>
    <p class="para">Duis autem vel eum iriure dolor in hendrerit in vulputate velit esse molestie consequat, vel illum dolore eu feugiat nulla facilisis at vero eros et accumsan et iusto odio dignissim qui blandit praesent luptatum zzril delenit augue duis dolore te feugait nulla facilisi. Lorem ipsum dolor sit amet, consectetuer adipiscing elit, sed diam nonummy nibh euismod tincidunt ut laoreet dolore magna aliquam erat volutpat.</p>
    <p class="para">Nam liber tempor cum soluta nobis eleifend option congue nihil imperdiet doming id quod mazim placerat facer possim assum. Lorem ipsum dolor sit amet, consectetuer adipiscing elit, sed diam nonummy nibh euismod tincidunt ut laoreet dolore magna aliquam erat volutpat. Ut wisi enim ad minim veniam, quis nostrud exerci tation ullamcorper suscipit lobortis nisl ut aliquip ex ea commodo consequat.</p>
    <p class="closing">Sincerely,</p>
    <span class="signature" role="img" aria-label="Handwritten signature of Daniel Whitford"></span>
  </section>

  <div class="footer-band" role="img" aria-label="Soft grey decorative footer area"></div>
  <div class="footer-strip"></div>

  <footer class="footer">
    2140 Ridgeview Court Atlanta, GA 30309<br>
    <b>P:</b> 404-555-0172 | <b>F:</b> 404-555-0188
  </footer>
</main>
</body>
</html>
```